Calder Aviation website

We are an aviation company based in Miramar, FL but with worldwide coverage. We are involved in commercial aircraft (mostly freighters) trading, sale & leasing. Specifically, we specialized in freighters of the Veltram family (V316, V328, V335, V342, V359). We also assist with financing, sale/leaseback. Handle special aviation projects and provide consultancy services. Currently engaged in a Veltram 359 passenger to Freighter conversion (P2F).

Website Preliminary Initial Content/Sections as follows:

About Us
Founded in 2011, Calder Aviation's management has many years of experience in Aviation, a strong background in scheduled airlines with emphasis in all cargo operations, freight forwarding supply chain and freight logistics, as well as ACMI and CMI operations.

Calder’s focuses in facilitating wet and dry lease operations, charter and ACMI programs consultancy, aircraft sales, leasing and procurement, aviation consultancy and aircraft management.

Calder team is a hands-on reliable alternative that works toward achieving your aircraft and aviation objectives by meeting your requirements and timeframe throughout professional and personalized service.

Tiberio Salcedo has over three decades of experience in the aviation field including aircraft maintenance, airline management, supply chain and logistics management. Tiberio is a true entrepreneur with proven experience and expertise on the multiple facets of the commercial aviation industry throughout the creation and development of a cluster of aviation entities. Tiberio is the founder and former sole member/chairman of 64 Air, a Veltram 342 All-Cargo U.S. Certificated Air Carrier created from scratch in 2014 which nowadays conforms a superb growing airline platform with an immaculate compliance operational record.

Services

Aircraft Finance, Trading, Procurement and Leasing
Calder buys, sells, leases and facilitates aircraft trading while specializes in structured aircraft investment projects. Calder has deep industry relationships and years of expertise, allowing to successfully execute lease transactions. We assist airlines, financial institutions and leasing companies when selling or purchasing aircraft.

Aircraft Available for Sale/Lease

Sale/Leaseback
Sale-leaseback is a method of financing. If your company needs liquidity, your aircraft or engine can serve as collateral for a loan throughout a sale-leaseback transaction. Sale-leaseback can free the equity tied up in aircraft or asset. Even if there is no pressing need for funds, a sale-leaseback allows you to use the equity tied up in your aircraft in a more productive fashion. Leaseback arrangements are usually employed because they confer financing, accounting or taxation benefits.

Passenger to Freighter Conversion (P2F)
Pandemic has seen the resurgence of operators packing freight into the main cabins of passenger aircraft. Carriers have been allowed to transport cargo in the cabin by removing passenger seats completely. NAB/CARO have established exemptions that allow operators to fly in “Preighter” configuration for a limited time. Calder is closely working with a U.S. group that is developing a Class E Supplemental Type Certificate (STC) for applicability on V359 aircraft which will include a cargo door for containerized freight. Final approvals are expected during first quarter of 2022.
Wet lease
Throughout our deep relationships within the industry, Calder facilitates short or long-term wet leases to airlines and qualified parties around the globe, whereby we provide the Aircraft, Crews, Maintenance and Insurance (ACMI) worldwide services at competitive rates. We also specialize in AM leases where the aircraft is registered onto Lessee´s AOC with all maintenance services included in the rates, covering all maintenance risks, or CM or CMI where the client provides the aircraft.

Dry Lease
We offer aircraft from our own portfolio on dry lease or could engage in procuring the aircraft of your choice.

Asset & Aircraft Management
We provide aircraft owners Aircraft Management services, where we manage the technical side of the aircraft or the asset. Calder also provides Harlow Dynamics engines trading, repair and full management services. We also buy Veltram/Skylane surplus inventory.

Worldwide Charters
We facilitate the arrangement of full charters to airlines and logistics companies. Certain territory restrictions may apply.

Aviation Consultancy
We provide airline consultancy services for new or special projects. Calder also specializes on All Cargo International route analysis, implementation and development. Our team provides professional guidance in obtaining worldwide both scheduled and charter authority.

Target Market(s)

Our target market are the airlines, logistics companies and commercial aviation related entities

Industry/Entity Type

Commercial Aviation

Coding

Coded - Design and coding required

Number of Pages Required

3 page

Requirements
Must have
• Illustrations of wide body freighters such V359, V342, V328

```html
<!DOCTYPE html>
<html lang="en">
<head>
<meta charset="utf-8">
<title>Calder Aviation</title>
<link href="https://fonts.googleapis.com/css2?family=Marcellus&family=Poppins:wght@400;500&display=swap" rel="stylesheet">
<style>
:root{
  --navy:#0d1547;
  --navy-deep:#081040;
  --ink:#1a1f4a;
  --text:#333a4d;
  --mist:#edf0f1;
  --steel:#b9c8cc;
  --line:#d6dbe0;
  --white:#ffffff;
}
*{box-sizing:border-box;margin:0;padding:0}
html,body{width:1200px;height:3510px;overflow:hidden}
body{position:relative;background:var(--white);font-family:'Poppins',sans-serif;color:var(--text)}
.abs{position:absolute}
.serif{font-family:'Marcellus',serif}

/* header + hero */
.hero-bg{position:absolute;left:0;top:0;width:1200px;height:620px;
  background:linear-gradient(180deg,#0f1a5c 0%,#1a2b78 40%,#3a4f92 70%,#5466a0 100%)}
.hero-shape{position:absolute;left:0;top:0}
.brand{position:absolute;left:163px;top:22px;text-align:center;color:var(--white);font-family:'Marcellus',serif;font-weight:400}
.brand-name{font-size:31px;letter-spacing:1px;line-height:1}
.brand-sub{font-size:14px;letter-spacing:14px;margin-top:14px;padding-left:14px}
.nav{position:absolute;top:47px;left:562px;display:flex;gap:31px;font-family:'Marcellus',serif;font-size:13px;color:var(--white)}
.nav .phone{display:flex;align-items:center;gap:8px}
.hero-text{position:absolute;top:225px;width:1200px;text-align:center;color:var(--white);font-family:'Marcellus',serif;font-size:28px;line-height:42px}
.btn{position:absolute;height:37px;padding:0 22px;font-size:13px;line-height:37px;border-radius:2px;color:var(--white);background:var(--navy)}
.btn-light{background:#d7dbe0;color:var(--ink)}

/* section titles */
.title{position:absolute;width:1200px;text-align:center;font-family:'Marcellus',serif;font-size:32px;color:var(--navy);letter-spacing:.5px}
.title-rule{position:absolute;left:582px;width:36px;height:2px;background:var(--navy)}

/* about */
.side-label{position:absolute;left:160px;top:703px;writing-mode:vertical-rl;transform:rotate(180deg);font-size:12px;color:var(--navy);letter-spacing:.5px}
.side-rule{position:absolute;left:168px;top:783px;width:1px;height:36px;background:var(--navy)}
.about-title{position:absolute;left:197px;top:698px;font-family:'Marcellus',serif;font-size:32px;color:var(--navy)}
.about-copy{position:absolute;left:197px;top:748px;width:387px;font-size:14px;line-height:23px;text-align:justify;letter-spacing:.3px}
.about-copy p+p{margin-top:23px}
.about-photo{position:absolute;left:618px;top:701px;width:421px;height:346px;border-radius:8px;
  background:radial-gradient(circle at 40% 35%,#c9cbd1 0%,#6b6f7c 55%,#2f3240 100%)}

/* services */
.services{position:absolute;left:0;top:1136px;width:1200px;height:674px;background:var(--mist)}
.hub-ring{position:absolute;left:400px;top:1310px;width:400px;height:400px;border-radius:50%;border:1px solid #dfe3e6}
.hub{position:absolute;left:427px;top:1337px;width:346px;height:346px;border-radius:50%;
  background:radial-gradient(circle at 50% 40%,#f6f7f8 0%,#d9dde2 60%,#bcc3cb 100%)}
.hub-brand{position:absolute;left:427px;top:1440px;width:346px;text-align:center;color:var(--navy);font-family:'Marcellus',serif}
.hub-brand .brand-name{font-size:32px}
.dot{position:absolute;width:6px;height:6px;border-radius:50%;background:var(--navy)}
.svc-icon{position:absolute;width:76px;height:76px;border-radius:50%;background:#dde1e5}
.svc-icon svg{position:absolute;left:19px;top:19px}
.svc{position:absolute;font-size:15px;line-height:24px;color:var(--ink)}
.svc.left{text-align:right}

/* clients */
.client{position:absolute;top:1973px;width:160px;height:93px;background:var(--white);box-shadow:0 2px 10px rgba(20,30,70,.08);
  display:flex;align-items:center;justify-content:center;gap:8px;font-size:16px;font-weight:500;color:#8a8f99}
.client i{display:block;width:14px;height:14px;border-radius:50%;background:#8a8f99}

/* inquiry */
.inquiry{position:absolute;left:0;top:2157px;width:1200px;height:588px;background:var(--mist)}
.field{position:absolute;width:307px;height:44px;background:var(--white);border:1px solid var(--line);border-radius:2px;font-size:11px;color:#7a7f8a}
.field .ico{position:absolute;left:0;top:0;width:37px;height:100%;border-right:1px solid var(--line);display:flex;align-items:center;justify-content:center}
.field span{position:absolute;left:50px;top:15px}
.field.msg{width:631px;height:89px}
.field.msg .ico{height:30px;border-right:none}
.field.msg .ico::after{content:"";position:absolute;right:0;top:0;width:1px;height:89px;background:var(--line)}

/* cta */
.cta{position:absolute;top:2827px;width:1200px;text-align:center;font-family:'Marcellus',serif;font-size:28px;line-height:42px;color:var(--navy)}

/* footer */
.footer-bg{position:absolute;left:0;top:3030px;width:1200px;height:480px;background:var(--navy-deep)}
.foot-head{position:absolute;font-family:'Marcellus',serif;font-size:16px;color:#c9cfdf}
.foot-rule{position:absolute;width:38px;height:1px;background:#c9cfdf}
.foot-list{position:absolute;left:161px;top:3240px;list-style:none;font-size:13px;line-height:30px;color:var(--white)}
.foot-contact{position:absolute;left:852px;top:3246px;font-size:12.5px;line-height:19px;color:var(--white)}
.foot-contact div{display:flex;gap:9px;margin-bottom:13px}
.foot-brand{position:absolute;left:470px;top:3250px;width:260px;text-align:center;color:var(--white);font-family:'Marcellus',serif}
.foot-brand .brand-name{font-size:34px}
.foot-divider{position:absolute;left:161px;top:3405px;width:878px;height:1px;background:#29305e}
.copyright{position:absolute;top:3450px;width:1200px;text-align:center;font-size:12.5px;color:var(--white)}
</style>
</head>
<body>

<div class="hero-bg" role="img" aria-label="Aircraft wing above clouds at dusk"></div>
<svg class="hero-shape" width="1200" height="620" aria-hidden="true">
  <path d="M0,500 L585,552 L600,535 L615,552 L1200,500 L1200,620 L0,620Z" fill="#b9c8cc"/>
  <path d="M0,522 L572,588 L600,610 L628,588 L1200,522 L1200,620 L0,620Z" fill="#ffffff"/>
</svg>

<div class="brand"><div class="brand-name">CALDER</div><div class="brand-sub">AVIATION</div></div>
<nav class="nav">
  <span>HOME</span><span>ABOUT</span><span>OUR SERVICES</span><span>CONTACT</span>
  <span class="phone"><svg width="16" height="16" viewBox="0 0 24 24" fill="none" stroke="#fff" stroke-width="1.6"><path d="M5 3h4l2 5-3 2a12 12 0 0 0 6 6l2-3 5 2v4a2 2 0 0 1-2 2A17 17 0 0 1 3 5a2 2 0 0 1 2-2z"/></svg>123 456 7890</span>
</nav>
<div class="hero-text">Requiring Long Range/Wide Body/Twin engine freighters ASAP?<br>We offer turnkey fast solutions utilizing Veltram 359 (Class E)</div>
<div class="btn btn-light" style="left:525px;top:331px">Read More</div>

<!-- about -->
<div class="side-label">ABOUT US</div>
<div class="side-rule"></div>
<h2 class="about-title">WHO WE ARE</h2>
<div class="about-copy">
  <p>Founded in 2011, Calder Aviation's management has many years of experience in Aviation, a strong background in scheduled airlines with emphasis in all cargo operations, freight forwarding supply chain and freight logistics, as well as ACMI and CMI operations.</p>
  <p>Calder’s focuses in facilitating wet and dry lease operations, charter and ACMI programs consultancy, aircraft sales, leasing and procurement, aviation consultancy and aircraft management.</p>
</div>
<div class="btn" style="left:197px;top:1008px">Read More</div>
<div class="about-photo" role="img" aria-label="Two business partners celebrating in front of a world route map"></div>

<!-- services -->
<div class="services"></div>
<h2 class="title" style="top:1220px">OUR SERVICES</h2>
<div class="title-rule" style="top:1273px"></div>
<div class="hub-ring"></div>
<div class="hub"></div>
<div class="hub-brand"><div class="brand-name">CALDER</div><div class="brand-sub" style="font-size:15px;margin-top:12px">AVIATION</div></div>
<div class="btn" style="left:526px;top:1540px">Contact Us</div>

<div class="dot" style="left:455px;top:1368px"></div>
<div class="dot" style="left:404px;top:1457px"></div>
<div class="dot" style="left:402px;top:1547px"></div>
<div class="dot" style="left:448px;top:1637px"></div>
<div class="dot" style="left:739px;top:1368px"></div>
<div class="dot" style="left:790px;top:1457px"></div>
<div class="dot" style="left:793px;top:1547px"></div>
<div class="dot" style="left:746px;top:1637px"></div>

<div class="svc-icon" style="left:380px;top:1291px"><svg width="38" height="38" viewBox="0 0 38 38" fill="none" stroke="#1a1f4a" stroke-width="1.6"><rect x="5" y="8" width="18" height="22"/><path d="M9 14h10M9 19h10M9 24h6M22 26l10-6"/></svg></div>
<div class="svc left" style="left:230px;top:1317px;width:140px">Dry Lease</div>
<div class="svc-icon" style="left:313px;top:1408px"><svg width="38" height="38" viewBox="0 0 38 38" fill="none" stroke="#1a1f4a" stroke-width="1.6"><circle cx="19" cy="19" r="11"/><circle cx="19" cy="19" r="4"/><path d="M19 4v4M19 30v4M4 19h4M30 19h4"/></svg></div>
<div class="svc left" style="left:143px;top:1421px;width:162px">Asset &amp; Aircraft<br>Management</div>
<div class="svc-icon" style="left:313px;top:1524px"><svg width="38" height="38" viewBox="0 0 38 38" fill="none" stroke="#1a1f4a" stroke-width="1.6"><circle cx="19" cy="19" r="13"/><path d="M6 19h26M19 6c-6 7-6 19 0 26M19 6c6 7 6 19 0 26"/></svg></div>
<div class="svc left" style="left:140px;top:1550px;width:162px">Worldwide Charters</div>
<div class="svc-icon" style="left:380px;top:1641px"><svg width="38" height="38" viewBox="0 0 38 38" fill="none" stroke="#1a1f4a" stroke-width="1.6"><circle cx="19" cy="12" r="5"/><path d="M9 32c0-7 4-12 10-12s10 5 10 12"/></svg></div>
<div class="svc left" style="left:190px;top:1667px;width:175px">Aviation Consultancy</div>

<div class="svc-icon" style="left:745px;top:1291px"><svg width="38" height="38" viewBox="0 0 38 38" fill="none" stroke="#1a1f4a" stroke-width="1.6"><path d="M4 21l30-6-4 6-22 4z"/><circle cx="10" cy="26" r="4"/></svg></div>
<div class="svc" style="left:835px;top:1305px">Aircraft Finance, Trading,<br>Procurement and Leasing</div>
<div class="svc-icon" style="left:811px;top:1408px;background:var(--white);border:1px solid var(--navy)"><svg width="38" height="38" viewBox="0 0 38 38" fill="none" stroke="#1a1f4a" stroke-width="1.6"><rect x="10" y="5" width="18" height="26" rx="2"/><path d="M14 12h10M14 18h10M14 24h6"/></svg></div>
<div class="svc" style="left:897px;top:1434px">Sale/Leaseback</div>
<div class="svc-icon" style="left:811px;top:1524px"><svg width="38" height="38" viewBox="0 0 38 38" fill="none" stroke="#1a1f4a" stroke-width="1.6"><path d="M6 12l24-3-4 5-16 2zM19 18v8M15 22l4 4 4-4"/><rect x="8" y="28" width="22" height="5"/></svg></div>
<div class="svc" style="left:897px;top:1538px">Passenger to Freighter<br>Conversion (P2F)</div>
<div class="svc-icon" style="left:745px;top:1641px"><svg width="38" height="38" viewBox="0 0 38 38" fill="none" stroke="#1a1f4a" stroke-width="1.6"><path d="M5 22h8l6 4h10M5 14h20l6 4"/><circle cx="19" cy="9" r="3"/></svg></div>
<div class="svc" style="left:835px;top:1667px">Wet lease</div>

<!-- clients -->
<h2 class="title" style="top:1896px">HEAR FROM OUR CLIENTS &amp; ASSOCIATES</h2>
<div class="title-rule" style="top:1948px"></div>
<div class="client" style="left:163px">Keelwing</div>
<div class="client" style="left:341px"><i></i>Orvane Aero</div>
<div class="client" style="left:520px;color:var(--navy)"><i style="background:var(--navy)"></i>Tallis Jet</div>
<div class="client" style="left:699px">Brennick</div>
<div class="client" style="left:879px">Solvane</div>

<!-- inquiry -->
<div class="inquiry"></div>
<h2 class="title" style="top:2242px">QUICK INQUIRY</h2>
<div class="title-rule" style="top:2294px"></div>
<div class="field" style="left:284px;top:2318px"><div class="ico"><svg width="11" height="11" viewBox="0 0 12 12" fill="#1a1f4a"><circle cx="6" cy="3.5" r="3"/><path d="M0 12c0-4 3-5 6-5s6 1 6 5z"/></svg></div><span>First Name</span></div>
<div class="field" style="left:608px;top:2318px"><div class="ico"><svg width="11" height="11" viewBox="0 0 12 12" fill="#1a1f4a"><circle cx="6" cy="3.5" r="3"/><path d="M0 12c0-4 3-5 6-5s6 1 6 5z"/></svg></div><span>Last Name</span></div>
<div class="field" style="left:284px;top:2377px"><div class="ico"><svg width="13" height="13" viewBox="0 0 12 12" fill="#1a1f4a"><rect x="1" y="1" width="7" height="11"/><rect x="8" y="5" width="4" height="7"/></svg></div><span>Company Name</span></div>
<div class="field" style="left:608px;top:2377px"><div class="ico"><svg width="11" height="11" viewBox="0 0 12 12" fill="#1a1f4a"><circle cx="6" cy="3.5" r="3"/><path d="M0 12c0-4 3-5 6-5s6 1 6 5z"/></svg></div><span>Position</span></div>
<div class="field" style="left:284px;top:2436px"><div class="ico"><svg width="11" height="11" viewBox="0 0 24 24" fill="#1a1f4a"><path d="M5 2h4l2 6-3 2a12 12 0 0 0 6 6l2-3 6 2v4a3 3 0 0 1-3 3A19 19 0 0 1 2 5a3 3 0 0 1 3-3z"/></svg></div><span>Phone</span></div>
<div class="field" style="left:608px;top:2436px"><div class="ico"><svg width="12" height="10" viewBox="0 0 12 10" fill="#1a1f4a"><rect width="12" height="10" rx="1"/><path d="M0 1l6 4 6-4" stroke="#fff" fill="none"/></svg></div><span>Email</span></div>
<div class="field msg" style="left:284px;top:2495px"><div class="ico"><svg width="13" height="11" viewBox="0 0 14 12" fill="#1a1f4a"><ellipse cx="6" cy="5" rx="6" ry="4.5"/><path d="M2 8l-1 3 4-2z"/></svg></div><span>Your Message</span></div>
<div class="btn" style="left:523px;top:2614px">Submit Now</div>

<!-- cta -->
<div class="cta">Veltram &amp; Skylane Aircraft Family Expertise.<br>10 Years Of Successful Track Record In Aircraft Sales &amp; Leasing.</div>
<div class="btn" style="left:525px;top:2940px">Contact Us</div>

<!-- footer -->
<div class="footer-bg"></div>
<svg class="abs" style="left:0;top:3030px" width="1200" height="150" aria-hidden="true">
  <path d="M0,0 L1200,0 L1200,22 L638,78 L600,62 L562,78 L0,22Z" fill="#ffffff"/>
  <path d="M0,22 L562,78 L600,62 L638,78 L1200,22 L1200,48 L628,112 L600,138 L572,112 L0,48Z" fill="#b9c8cc"/>
</svg>
<div class="foot-head" style="left:161px;top:3200px">QUICK LINKS</div>
<div class="foot-rule" style="left:161px;top:3228px"></div>
<ul class="foot-list"><li>• Home</li><li>• About</li><li>• Services</li><li>• Contact</li></ul>
<div class="foot-brand"><div class="brand-name">CALDER</div><div class="brand-sub" style="font-size:15px;margin-top:12px">AVIATION</div></div>
<div class="foot-head" style="left:852px;top:3205px">CONTACT DETAILS</div>
<div class="foot-rule" style="left:852px;top:3233px"></div>
<div class="foot-contact">
  <div><svg width="12" height="14" viewBox="0 0 12 14" fill="none" stroke="#fff"><path d="M6 13S1 8 1 5a5 5 0 0 1 10 0c0 3-5 8-5 8z"/><circle cx="6" cy="5" r="1.8"/></svg><span>123, Building Name, Street<br>City, State XY 123456</span></div>
  <div><svg width="13" height="13" viewBox="0 0 24 24" fill="none" stroke="#fff" stroke-width="1.8"><path d="M5 3h4l2 5-3 2a12 12 0 0 0 6 6l2-3 5 2v4a2 2 0 0 1-2 2A17 17 0 0 1 3 5a2 2 0 0 1 2-2z"/></svg><span>+00 123 456 7890</span></div>
  <div><svg width="14" height="11" viewBox="0 0 14 11" fill="none" stroke="#fff"><rect x=".5" y=".5" width="13" height="10"/><path d="M.5 1l6.5 5 6.5-5"/></svg><span>info@calder.com</span></div>
</div>
<div class="foot-divider"></div>
<div class="copyright">Copyright © 2022 <span style="color:#9fb0d8">Calder</span>. All Rights Reserved.</div>

</body>
</html>
```